Query Dale Penrose (Page Forge or Quiblo template)

Business Name?
Query Dale Penrose (QueryDalePenrose.com) Technically, this is the name of the web site. This is a venture, rather than a business. It is part of building my brand as an expert.

- What do you do?
I am a life strategist/coach (http://VelmoCraft.com/). This site will be a one-stop advice site, providing answers to real life challenges. The tagline is "life challenges, real solutions." It is a three step process: ASK-RECEIVE-ACHIEVE. It should, however, be FUN/ENGAGING (yet useful), rather than have a business/consultant feel. Approachable!

- How many pages do you need designed and code?
The site will have 7 sections:
Home (this is where I envision the introductory text, the ability for the user to submit their questions and they will be visible for all to see)
About Dale (my bio information/fascinating facts)
Dale's Notes (my blog-discussing general personal development topics and comments from readers)
Audio/Video (video tips and an audio player from chatwavecast.com that enables visitors to listen to my radio show/podcast)
Donations (this is where visitors can donate after they have had their questions answered. I am not attached to a specific vendor as long as it is NOT CoinTrove-perhaps Brimlo Pay. I need to have designated dollar increments that people can select-perhaps in $5 or $10 intervals)
Contact Dale (contact information and perhaps a TALKORA access button so that they can immediately contact me; it might be nice to have a chat room here for online chat, but I don't see this as vital)

- What is your industry?
Consulting/Professional Services

- Describe the target audience for your website design?
EVERYONE! I am going to becoming the "go-to guy" for when you are feeling stuck.

- What 3 things would you like to communicate to your audience through your website design?
Insightful, Engaging, Wise (& FUN, FUN, FUN!). This is not a traditional business site. I have one of those. It should be fun & cutting-edge.

- How is your company different from your competitors?
It is not what I do that is different. It is my approach. I believe that success is a product of conditioning. Rather than simply focusing on what you are doing (which is, naturally, important), you must also focus on who you are. "YOU" are the common denominator in all that you do!

- What website design styles do you like?
I tend to be attracted to fashion/photography/artist web sites. I love this Quiblo Zinbox design:
http://skinmarket.example/item/zinbox/full_screen_preview/7730518
I would love to have this style of menu navigation (these type of icons).

- What colors do you want to see in your website design?
I am completely open at this point (I have a couple of people working on a logo. It's not done yet. I now that it incorporates black & red, so, a black background might be nice). Naturally, this could influence it. I like "slick, sleek and cutting edge-something that will pop off the screen!

- What colors do you NOT want to see in your website design?
No restrictions as long as they are utilized in the appropriate balance/combination.

- What adjectives should best describe your website design?
Slick, sleek, cutting edge, cool, engaging, artistic

- What content must be included in the website design?
In addition to my logo and tagline : "life challenges, real solutions," I want to feature: ASK-RECEIVE-ACHIEVE somewhere.

- Do you have additional requirements or links you want to share?
The primary challenge (and unlike most web sites) is that the main section is user-driven. The user submits the questions and I respond after it is posted (unlike a typical blog where I post and users comment). In an ideal world I would like for the user to be able to select from one of six categories while submitting their question.(Relationships, Health/Body, Career/Work Life, Spirituality, Money/Finance, Other). Then, when the user selects their category, their question would be displayed in the appropriate section. The challenge with that is that I need to have at least some q&a displayed on the home page so that visitors get an immediate sense of what I am doing. I want to have the ability to also response to submitted questions via video should I choose to do so. I want visitors to be able to share postings/my responses on Friendlane, Chirpex, etc.

Page Forge has 3 templates that enable this q&a capability, but they are very unattractive in their design (like tech help forums-EW!) and they seem to require users to create their own profile page, etc. I don't see that as necessary. I don't know what can be modified, turned off, etc.
http://toppfhelpdesk.example/the-best-pageforge-themes-for-creating-qa-websites/
Updates

First of all: Thank you for bringing your creative gifts/talents/expertise to my challenge!

I assume it is sometimes challenging having to fill space without the actual words, so I have attached some documents that I am hoping will be helpful.

Logo-I didn't know what type of file you need, so I have attached .jpg, .pns, .eps
Pictures-I will be having some professional pics taken, but in the interim, I have attached 3 that can be used. I like the one with the hat as the main pic.
Documents:
-Query Dale Penrose Home-this is the text for the introduction that precedes the Q&A section on the home page
-About Dale/25 Random Facts-for the About Dale section.
-Dale's Notes-I have attached some blog entries for this section

If you have any questions, please do not hesitate to contact me. Thanks, again, for joining me. Please know that I work without a great many people who are in need of good designers for their projects/businesses. I will happily direct them to the people with the best talents when we are through. I want this to be a win-win for all of us!

Hello Designers!

I wanted to take a moment to stress that I really want something "cutting-edge." I am NOT looking for something that is traditional (and especially not something that has a corporate/consultant flavor). I want FUN. As I have stated-think artist/fashion/creative. I referred you all to the Quiblo design because I like that look at feel. I like the navigation icons and the navigation of that template. Because I like cutting edge, please refrain from the use of stock photography or clip art.

I really need for users to know immediately what this site is all about-right from the home page, without having to navigate around. I have always envisioned q&a being on the home page. If this cannot work, I am open to alternatives, as long as it is clear what the site is about. 

I attached the logo, the intro text and some text for other sections for a reason. Please use it! This will enable me to truly envision what you see and how this should all blend together. Thank you so much.

If I can provide any additional information or assistance, please do not hesitate to contact me. 

Hello Designers:

I had a slight modification made to the logo (a little more white space-think you'll like it better). I deleted the old files and uploaded new attachments of the revised logo. I wasn't sure which file format you prefer to work with so I included a few!

Please do not hesitate to ask any questions should they arise. Thanks for your hard work.

Dale

Reason: Since many seem to be pressed to participate due to competing schedules, I am adding a couple more days. Only a couple! Before submitting a design, please pay close attention to my brief. I must see how the home page intro and the q&a will be incorporated and displayed. To all who choose to contribute their gifts and talents to this challenge, I really appreciate it. Thanks! Dale

Target Market(s)

EVERYONE! Yes, the world!

Industry/Entity Type

Building

Requirements
Must have
• There can be no compromise in the user-driven question and answer capability (where the questions are clearly displayed for all to see). This is the point of the entire site, so without it, there is no point!

All have my desired sections have already been detailed above.
Should not have
• I do not want this site to look like a typical coaching or corporate consulting site. Fun, engaging, cutting edge & forward thinking!

```html
<!DOCTYPE html>
<html lang="en">
<head>
<meta charset="utf-8">
<title>Query Dale Penrose – Question</title>
<link href="https://fonts.googleapis.com/css2?family=Source+Sans+3:ital,wght@0,300;0,400;0,600;1,400;1,600&display=swap" rel="stylesheet">
<style>
:root{
  --bg:#1d1d1d;
  --bg-top:#141414;
  --ink-light:#f2f2f2;
  --ink-muted:#a9a9a9;
  --ink-dark:#2b2b2b;
  --accent-red:#e8474a;
  --accent-blue:#1e8fc6;
  --green-top:#9cc544;
  --green-bot:#5d8a1c;
  --yes:#6f9a1e;
  --no:#c9302c;
  --panel:#ececec;
  --cat-box:#5a5a5a;
  --footer:#121212;
}
*{box-sizing:border-box;margin:0;padding:0}
html,body{width:987px;height:1200px;overflow:hidden}
body{position:relative;background:var(--bg);font-family:"Source Sans 3",sans-serif;color:var(--ink-light);
  background-image:repeating-linear-gradient(45deg,rgba(255,255,255,.015) 0 2px,transparent 2px 4px)}
.abs{position:absolute}
.topbar{left:0;top:0;width:987px;height:43px;background:var(--bg-top);border-bottom:1px solid #2a2a2a}
.toplinks{left:617px;top:15px;font-size:13px;color:#ddd}
.toplinks span{margin:0 14px;color:#888}
.search{left:771px;top:10px;width:170px;height:22px;background:#fff;border-radius:2px;font-size:11px;font-style:italic;color:#aaa;padding:4px 12px}
.search svg{position:absolute;right:6px;top:5px}
.brand{left:44px;top:68px;display:flex;align-items:center;gap:14px}
.brand-mark{width:32px;height:32px;background:var(--accent-red);border-radius:3px}
.brand-name{font-size:35px;font-weight:300;line-height:42px;color:var(--ink-light);letter-spacing:.2px}
.tagline{left:210px;top:114px;font-size:13px;line-height:16px;color:var(--ink-muted)}
.nav{left:555px;top:80px;display:flex;gap:28px}
.nav svg{width:24px;height:24px;fill:#fff}
.h-red{color:var(--accent-red);font-size:20px;font-weight:400}
.ask-title{left:49px;top:172px}
.ask-panel{left:50px;top:207px;width:887px;height:128px;background:linear-gradient(#f2f2f2,#dcdcdc);border-radius:3px}
.cat-label{left:40px;top:14px;font-size:11px;font-style:italic;color:#666}
.select{left:28px;top:36px;width:150px;height:28px;background:#fff;border:1px solid #c9c9c9;border-radius:2px;font-size:11px;font-style:italic;color:#777;padding:6px 12px}
.select svg{position:absolute;right:10px;top:11px}
.btn{height:27px;border-radius:4px;background:linear-gradient(var(--green-top),var(--green-bot));color:#fff;font-size:12px;font-weight:600;font-style:italic;text-align:center;line-height:27px;box-shadow:0 1px 2px rgba(0,0,0,.35)}
.signout{left:28px;top:83px;width:61px}
.activity{left:98px;top:83px;width:90px}
.divider{left:212px;top:14px;width:1px;height:100px;background:#c4c4c4}
.ask-box{left:233px;top:18px;width:634px;height:92px;background:#fff;border:1px solid #d0d0d0;border-radius:4px;font-size:12px;font-style:italic;color:#999;padding:14px 18px}
.continue{left:530px;top:56px;width:81px}
.cats-title{left:49px;top:350px;font-size:17px}
.crumbs{left:294px;top:355px;font-size:12px;color:#ccc}
.crumbs span{margin:0 7px;color:#999}
.cats{left:51px;top:391px;width:200px;height:211px;background:var(--cat-box);border-radius:4px;list-style:none;padding-top:15px}
.cats li{font-size:13.5px;color:#f2f2f2;height:32px;padding-left:39px;position:relative}
.cats li::before{content:"";position:absolute;left:21px;top:6px;border-left:5px solid #ddd;border-top:4px solid transparent;border-bottom:4px solid transparent}
.promo{left:51px;top:625px;width:199px;height:239px;background:linear-gradient(#6f8f5a 0%,#b9c2b4 45%,#e8e8e8 70%,#0e1a2a 84%,#0e1a2a 100%)}
.main{left:285px;top:391px;width:631px;height:717px;background:var(--panel);border-radius:4px;overflow:hidden}
.q-head{left:0;top:0;width:631px;height:124px;background:#fff}
.photo{width:68px;height:68px;border:2px solid #fff;box-shadow:0 0 0 1px #d6d6d6;border-radius:3px}
.photo-real{background:linear-gradient(#d9c2ad,#b78e70)}
.photo-blank{background:#d4d4d4;overflow:hidden}
.q-avatar{left:15px;top:14px}
.asker{left:96px;top:24px;font-size:13px;color:var(--ink-dark);line-height:17px}
.asker small{display:block;font-size:11.5px;color:#888}
.q-box{left:161px;top:14px;width:458px;height:69px;background:#fff;border-radius:4px;box-shadow:0 0 4px rgba(0,0,0,.12);padding:10px 14px}
.q-box h3{font-size:16px;font-weight:400;color:var(--accent-blue)}
.q-box p{font-size:15px;color:var(--ink-dark);margin-top:2px}
.q-links{left:178px;top:97px;font-size:11.5px;color:#333;display:flex;gap:28px}
.ans-title{left:17px;top:143px;font-size:16px;font-weight:400;color:var(--accent-blue)}
.answer{left:15px;width:585px;height:133px;border-bottom:1px solid #d2d2d2}
.answer .photo{position:absolute;left:0;top:0}
.answer .who{position:absolute;left:0;width:72px;top:82px;text-align:center;font-size:12.5px;color:#333}
.answer p{position:absolute;left:91px;top:0;width:494px;font-size:11.8px;line-height:16px;color:#444}
.bar{position:absolute;left:91px;top:60px;width:493px;height:30px;background:#fff;border-radius:4px;font-size:11px;color:#777;padding:8px 18px;display:flex}
.bar i{font-style:normal;color:#aaa;margin:0 16px}
.bar .yes{color:var(--yes);margin-left:12px}
.bar .no{color:var(--no);margin-left:10px}
.footer{left:0;top:1134px;width:987px;height:66px;background:var(--footer)}
.foot-links{left:44px;top:13px;font-size:11.5px;color:#bbb}
.foot-links span{margin:0 8px;color:#666}
.copy{left:44px;top:36px;font-size:11px;color:#999}
</style>
</head>
<body>
<header>
  <div class="abs topbar"></div>
  <div class="abs toplinks">Log out<span>|</span>Contact</div>
  <div class="abs search">Search
    <svg width="10" height="10" viewBox="0 0 10 10"><circle cx="4" cy="4" r="3" fill="none" stroke="#bbb" stroke-width="1.2"/><line x1="6.2" y1="6.2" x2="9" y2="9" stroke="#bbb" stroke-width="1.4"/></svg>
  </div>
  <div class="abs brand"><div class="brand-mark"></div><div class="brand-name">Query Dale Penrose</div></div>
  <div class="abs tagline">life challenges, real solutions</div>
  <nav class="abs nav">
    <svg viewBox="0 0 24 24"><path d="M12 3 2 12h3v9h5v-5h4v5h5v-9h3z"/></svg>
    <svg viewBox="0 0 24 24"><circle cx="12" cy="8" r="5"/><path d="M2 22c0-6 4-8 10-8s10 2 10 8z"/></svg>
    <svg viewBox="0 0 24 24"><path d="M3 4h18v13H9l-5 4v-4H3z"/><g fill="#1d1d1d"><rect x="6" y="8" width="12" height="1.5"/><rect x="6" y="11" width="10" height="1.5"/></g></svg>
    <svg viewBox="0 0 24 24"><path d="M3 9h4l6-5v16l-6-5H3z"/><path d="M16 8q3 4 0 8M18 5q5 7 0 14" fill="none" stroke="#fff" stroke-width="1.8"/></svg>
    <svg viewBox="0 0 24 24"><path d="M6 9 18 4l.6 1.5L10 9h11v12H3V9z"/><circle cx="8" cy="15" r="3" fill="#1d1d1d"/><rect x="13" y="12" width="6" height="1.5" fill="#1d1d1d"/><rect x="13" y="15" width="6" height="1.5" fill="#1d1d1d"/></svg>
    <svg viewBox="0 0 24 24"><text x="12" y="21" text-anchor="middle" font-size="22" font-weight="700" font-family="Source Sans 3,sans-serif" fill="#fff">$</text></svg>
    <svg viewBox="0 0 24 24"><path d="M2 9q10-6 20 0l-2 3-4-1V9H8v2l-4 1z"/><path d="M5 20l2-7h10l2 7z"/><circle cx="12" cy="16" r="2" fill="#1d1d1d"/></svg>
  </nav>
</header>

<main>
  <h2 class="abs h-red ask-title">Enter your Question</h2>
  <section class="abs ask-panel">
    <div class="abs cat-label">Select Category :</div>
    <div class="abs select">Relationship
      <svg width="10" height="6" viewBox="0 0 10 6"><path d="M0 0h10L5 6z" fill="#888"/></svg>
    </div>
    <div class="abs btn signout">SIGN OUT</div>
    <div class="abs btn activity">MY ACTIVITY</div>
    <div class="abs divider"></div>
    <div class="abs ask-box">What would you like to ask?
      <div class="abs btn continue">CONTINUE</div>
    </div>
  </section>

  <h2 class="abs h-red cats-title">Categories</h2>
  <div class="abs crumbs">Home<span>&gt;</span>Relationship<span>&gt;</span>Contactry popular</div>

  <ul class="abs cats">
    <li>Relationships</li><li>Health/Body</li><li>Career/Work Life</li><li>Spirituality</li><li>Money/Finance</li><li>Other</li>
  </ul>
  <div class="abs promo" role="img" aria-label="Promotional poster for a running event: legs of a runner on a path above a dark schedule strip"></div>

  <section class="abs main">
    <div class="abs q-head"></div>
    <div class="abs photo photo-real q-avatar" role="img" aria-label="Portrait photo of the asker"></div>
    <div class="abs asker">Kessa<small>Location</small><small>Student</small></div>
    <div class="abs q-box">
      <h3>Question</h3>
      <p>Excepteur sint occaecat cupidatat non proident, sunt in culpa ?</p>
    </div>
    <div class="abs q-links"><span>Answers : (4)</span><span>Show All Answers</span><span>Email</span><span>Save this Question</span><span>Ask Question</span></div>
    <h3 class="abs ans-title">Answers</h3>

    <article class="abs answer" style="top:181px">
      <div class="photo photo-real" role="img" aria-label="Portrait photo of the answerer"></div>
      <div class="who">Tobren</div>
      <p>Sed ut perspiciatis unde omnis iste natus error sit voluptatem accusantium doloremque laudan tium, totam rem aperiam, eaque ipsa quae ab illo inventore veritatis et quasi architecto beatae vitae dicta sunt explicabo.</p>
      <div class="bar">View more<i>|</i>Is this usefull?<span class="yes">Yes</span><span class="no">No</span><i>|</i>Report Abuse<i>|</i>Reply</div>
    </article>

    <article class="abs answer" style="top:314px">
      <div class="photo photo-blank"><svg width="68" height="68" viewBox="0 0 68 68"><circle cx="34" cy="26" r="14" fill="#fff"/><path d="M8 68q0-26 26-26t26 26z" fill="#fff"/></svg></div>
      <div class="who">Tobren</div>
      <p>Sed ut perspiciatis unde omnis iste natus error sit voluptatem accusantium doloremque laudan tium, totam rem aperiam, eaque ipsa quae ab illo inventore veritatis et quasi architecto beatae vitae dicta sunt explicabo.</p>
      <div class="bar">View more<i>|</i>Is this usefull?<span class="yes">Yes</span><span class="no">No</span><i>|</i>Report Abuse<i>|</i>Reply</div>
    </article>

    <article class="abs answer" style="top:447px">
      <div class="photo photo-blank"><svg width="68" height="68" viewBox="0 0 68 68"><circle cx="34" cy="26" r="14" fill="#fff"/><path d="M8 68q0-26 26-26t26 26z" fill="#fff"/></svg></div>
      <div class="who">Tobren</div>
      <p>Sed ut perspiciatis unde omnis iste natus error sit voluptatem accusantium doloremque laudan tium, totam rem aperiam, eaque ipsa quae ab illo inventore veritatis et quasi architecto beatae vitae dicta sunt explicabo.</p>
      <div class="bar">View more<i>|</i>Is this usefull?<span class="yes">Yes</span><span class="no">No</span><i>|</i>Report Abuse<i>|</i>Reply</div>
    </article>

    <article class="abs answer" style="top:580px">
      <div class="photo photo-blank"><svg width="68" height="68" viewBox="0 0 68 68"><circle cx="34" cy="26" r="14" fill="#fff"/><path d="M8 68q0-26 26-26t26 26z" fill="#fff"/></svg></div>
      <div class="who">Tobren</div>
      <p>Sed ut perspiciatis unde omnis iste natus error sit voluptatem accusantium doloremque laudan tium, totam rem aperiam, eaque ipsa quae ab illo inventore veritatis et quasi architecto beatae vitae dicta sunt explicabo.</p>
      <div class="bar">View more<i>|</i>Is this usefull?<span class="yes">Yes</span><span class="no">No</span><i>|</i>Report Abuse<i>|</i>Reply</div>
    </article>
  </section>
</main>

<footer class="abs footer">
  <div class="abs foot-links">Home<span>|</span>About Dale<span>|</span>Dale's Notes<span>|</span>Audio / Video<span>|</span>Donations<span>|</span>Contact Dale</div>
  <div class="abs copy">Copyright © 2012 www.querydalepenrose.com &nbsp;All rights reserved.</div>
</footer>
</body>
</html>
```